Seeking funky, innovative business cards

I am looking to refresh our current business cards to something more engaging, visual and impactful. We are a management consultancy firm, see website (www.larkstone-partners.com.au). I've included our colour scheme, sample of the slides we use and our old business cards. We would like our cards to have icons. The card should display:- Name- Title- Mobile number- Address- Email address- Website - Company logo- Our purpose statement "we shape the finest rooms in town to thrive"

Contact Information for Business Card

Brennan Ulfsson
Consultant
0468 927 341
Level 7, 218 Wexley Street, Larkfield 3184
brennan@larkstone-partners.com.au
www.larkstone-partners.com.au

Purpose statement "we shape the finest rooms in town to thrive"
LOGO available in google images

Font styles to use
Other font styles liked:
• Open Sans Light, Bebas Neue (open to other cool foints)

Colors
ffc214
5c5c5c
f5f5f5
fefefe

Requirements
Must have
• - Name
• - Title
• - Mobile number
• - Address
• - Email address
• - Website
• - Company logo
• - Our purpose statement "we shape the finest rooms in town to thrive"
Nice to have
• - Icons
• - Colour (see our colour scheme"

```html
<!DOCTYPE html>
<html lang="en">
<head>
<meta charset="utf-8">
<title>Larkstone Partners – Business Cards</title>
<link href="https://fonts.googleapis.com/css2?family=Open+Sans:wght@300;400;600&display=swap" rel="stylesheet">
<style>
  :root {
    --backdrop: #151617;
    --card: #222426;
    --accent: #ffc214;
    --ink: #fefefe;
    --ink-soft: #f5f5f5;
    --muted: #5c5c5c;
  }
  * { box-sizing: border-box; margin: 0; padding: 0; }
  html, body {
    width: 1200px; height: 800px; overflow: hidden;
    background: var(--backdrop);
    font-family: "Open Sans", Arial, sans-serif;
    color: var(--ink);
  }
  .stage {
    width: 1200px; height: 800px;
    display: flex; align-items: center; justify-content: center; gap: 40px;
  }
  .card {
    position: relative;
    width: 540px; height: 309px;
    background: var(--card);
    box-shadow: 0 18px 40px rgba(0,0,0,.55);
    overflow: hidden;
  }
  .brand { display: flex; align-items: center; gap: 10px; }
  .brand__dot {
    width: 14px; height: 14px; border-radius: 50%;
    background: var(--accent); flex: none;
  }
  .brand__name {
    font-weight: 300; color: var(--ink);
    letter-spacing: -0.5px; white-space: nowrap;
  }

  /* Front */
  .card--front {
    display: flex; flex-direction: column;
    align-items: center; justify-content: center; gap: 14px;
  }
  .card--front .brand__name { font-size: 44px; }
  .purpose {
    font-size: 15px; font-weight: 600; color: var(--ink-soft);
    letter-spacing: .2px; white-space: nowrap;
  }

  /* Back */
  .card--back .brand {
    position: absolute; top: 44px; right: 34px;
  }
  .card--back .brand__name { font-size: 34px; }
  .person { position: absolute; left: 34px; top: 140px; }
  .person__name { font-size: 24px; font-weight: 600; line-height: 1.15; white-space: nowrap; }
  .person__title { font-size: 15px; color: var(--accent); font-weight: 400; line-height: 1.3; }
  .divider {
    position: absolute; left: 34px; right: 34px; top: 198px;
    height: 1.5px; background: var(--accent);
  }
  .contacts {
    position: absolute; left: 34px; top: 212px;
    list-style: none; display: flex; flex-direction: column; gap: 5px;
  }
  .contacts li {
    display: flex; align-items: center; gap: 9px;
    font-size: 13.5px; line-height: 18px; color: var(--ink-soft); white-space: nowrap;
  }
  .contacts svg { width: 18px; height: 18px; flex: none; }
  .address {
    position: absolute; right: 34px; top: 212px;
    font-size: 13px; line-height: 1.4; text-align: right;
    color: var(--ink-soft); font-style: normal; white-space: nowrap;
  }
</style>
</head>
<body>
<main class="stage">

  <section class="card card--front">
    <div class="brand">
      <span class="brand__dot"></span>
      <span class="brand__name">Larkstone Partners</span>
    </div>
    <p class="purpose">we shape the finest rooms in town to thrive</p>
  </section>

  <section class="card card--back">
    <div class="brand">
      <span class="brand__dot"></span>
      <span class="brand__name">Larkstone Partners</span>
    </div>

    <div class="person">
      <h1 class="person__name">Brennan Ulfsson</h1>
      <p class="person__title">Consultant</p>
    </div>

    <div class="divider"></div>

    <ul class="contacts">
      <li>
        <svg viewBox="0 0 20 20" aria-hidden="true">
          <circle cx="10" cy="10" r="10" fill="#ffc214"/>
          <path d="M7 5.5l1.6 2.4-1 1.1a6 6 0 0 0 3.4 3.4l1.1-1 2.4 1.6-.8 1.6c-4 .2-8.4-4.2-8.2-8.2z" fill="#222426"/>
        </svg>
        0468 927 341
      </li>
      <li>
        <svg viewBox="0 0 20 20" aria-hidden="true">
          <circle cx="10" cy="10" r="10" fill="#ffc214"/>
          <rect x="5" y="6.5" width="10" height="7" fill="#222426"/>
          <path d="M5 6.5l5 4 5-4" fill="none" stroke="#ffc214" stroke-width="1"/>
        </svg>
        brennan@larkstone-partners.com.au
      </li>
      <li>
        <svg viewBox="0 0 20 20" aria-hidden="true">
          <circle cx="10" cy="10" r="10" fill="#ffc214"/>
          <g fill="none" stroke="#222426" stroke-width="1.1">
            <circle cx="10" cy="10" r="5"/>
            <ellipse cx="10" cy="10" rx="2.2" ry="5"/>
            <path d="M5 10h10"/>
          </g>
        </svg>
        www.larkstone-partners.com.au
      </li>
    </ul>

    <address class="address">
      Level 7, 218 Wexley Street<br>Larkfield 3184
    </address>
  </section>

</main>
</body>
</html>
```